TALMORK

The business want a professional looking business card. We have a scetch we will add but want the extra upgrade, and would like more suggestions for variations of our business cards.

```html
<!DOCTYPE html>
<html lang="en">
<head>
<meta charset="utf-8">
<title>TALMORK business card</title>
<link href="https://fonts.googleapis.com/css2?family=Cinzel:wght@600&family=Lato:wght@400&family=Vidaloka&display=swap" rel="stylesheet">
<style>
  :root {
    --backdrop: #8e8e8e;
    --card: #1e1e1e;
    --gold: #c9a24a;
    --text-light: #dcdcdc;
    --emboss-top: #3a3a3a;
    --emboss-bottom: #121212;
  }
  html, body {
    margin: 0;
    padding: 0;
    width: 1200px;
    height: 1200px;
    overflow: hidden;
    background: var(--backdrop);
  }
  .canvas {
    position: relative;
    width: 1200px;
    height: 1200px;
  }
  .card {
    position: absolute;
    top: 280px;
    width: 366px;
    height: 642px;
    background: var(--card);
    border-radius: 16px;
    overflow: hidden;
  }
  .card--front { left: 197px; }
  .card--back { left: 641px; }

  /* Front */
  .brand-dot {
    position: absolute;
    left: 50%;
    top: 268px;
    width: 40px;
    height: 40px;
    margin-left: -20px;
    border-radius: 50%;
    background: var(--gold);
  }
  .brand-name {
    position: absolute;
    left: 0;
    right: 0;
    top: 372px;
    margin: 0;
    text-align: center;
    font-family: "Cinzel", serif;
    font-weight: 600;
    font-size: 34px;
    letter-spacing: 6px;
    color: var(--gold);
  }
  .brand-since {
    position: absolute;
    left: 0;
    right: 0;
    top: 431px;
    text-align: center;
    font-family: "Lato", sans-serif;
    font-size: 7px;
    letter-spacing: 4px;
    color: var(--text-light);
  }

  /* Back */
  .emboss-area {
    position: absolute;
    left: 0;
    top: 0;
    width: 366px;
    height: 360px;
    background: radial-gradient(ellipse at 50% 40%, var(--emboss-top) 0%, #262626 45%, var(--card) 75%);
  }
  .person-name {
    position: absolute;
    left: 0;
    right: 0;
    top: 392px;
    margin: 0;
    text-align: center;
    font-family: "Vidaloka", serif;
    font-weight: 400;
    font-size: 27px;
    color: var(--gold);
  }
  .person-role {
    position: absolute;
    left: 0;
    right: 0;
    top: 426px;
    text-align: center;
    font-family: "Lato", sans-serif;
    font-size: 16px;
    color: var(--text-light);
  }
  .contact-divider {
    position: absolute;
    left: 66px;
    width: 234px;
    top: 470px;
    height: 16px;
  }
  .contact-list {
    position: absolute;
    left: 0;
    right: 0;
    top: 510px;
    margin: 0;
    padding: 0;
    list-style: none;
    text-align: center;
    font-family: "Lato", sans-serif;
    font-size: 15px;
    line-height: 22.5px;
    color: var(--text-light);
  }
</style>
</head>
<body>
<main class="canvas">
  <section class="card card--front">
    <div class="brand-dot"></div>
    <h1 class="brand-name">TALMORK</h1>
    <div class="brand-since">SINCE 2026</div>
  </section>

  <section class="card card--back">
    <div class="emboss-area" role="img" aria-label="Large embossed brand decoration in dark tones"></div>
    <h2 class="person-name">Aksel Vinter Dahlberg</h2>
    <div class="person-role">CEO &amp; Founder</div>
    <svg class="contact-divider" viewBox="0 0 234 16" aria-hidden="true">
      <line x1="0" y1="8" x2="72" y2="8" stroke="var(--gold)" stroke-width="1.2"/>
      <line x1="162" y1="8" x2="234" y2="8" stroke="var(--gold)" stroke-width="1.2"/>
      <!-- phone -->
      <path d="M84 2.5c1 0 1.6.2 2 1.2l.8 2c.2.6 0 1-.5 1.4l-.8.6c.6 1.4 1.6 2.5 3 3.2l.7-.8c.4-.5.9-.6 1.4-.4l2 .9c.8.4 1 1 .9 1.9-.3 1.2-1.4 2-2.6 1.9C85.6 13.8 80.7 9 80.6 4.4c0-1 .9-1.9 2-1.9z" fill="var(--gold)"/>
      <!-- envelope -->
      <rect x="110" y="3" width="14" height="10" rx="1" fill="var(--gold)"/>
      <path d="M110.5 3.8 117 9l6.5-5.2" fill="none" stroke="var(--card)" stroke-width="1.1"/>
      <!-- globe -->
      <circle cx="145" cy="8" r="6.3" fill="none" stroke="var(--gold)" stroke-width="1.4"/>
      <ellipse cx="145" cy="8" rx="2.6" ry="6.3" fill="none" stroke="var(--gold)" stroke-width="1"/>
      <line x1="138.7" y1="8" x2="151.3" y2="8" stroke="var(--gold)" stroke-width="1"/>
    </svg>
    <ul class="contact-list">
      <li>004790001234</li>
      <li>talmork.llc@postmail.com</li>
      <li>www.talmork.llc</li>
    </ul>
  </section>
</main>
</body>
</html>
```